Business Card Design

We provide services doing multiple jobs in the construction industry.Please note: The company name needs to be ROCK SOLID BUILDING SERVICESAttached logo was an example of what we wanted. Can you change up the colors?

Industry/Entity Type

Construction

Contact Information for Business Card

ROCK SOLID BUILDING SERVICES5401 HUDSON BEND RDAUSTIN, TX 78734(512)243-6854ROCKSOLIDBUILDINGSERVICES@GMAIL.COM

```html
<!DOCTYPE html>
<html lang="en">
<head>
<meta charset="utf-8">
<title>Pearlwood Framing Works – Business Card</title>
<link rel="stylesheet" href="https://fonts.googleapis.com/css2?family=Exo+2:wght@400;600;800&display=swap">
<style>
  :root {
    --page: #e9e9ec;
    --navy-light: #2e2c86;
    --navy-dark: #141248;
    --white: #ffffff;
    --ink: #1d1b5e;
    --grey-light: #c9c9cd;
    --grey-mid: #76767b;
    --charcoal: #2c2c30;
    --accent: #2a2890;
    --back-top: #ffffff;
    --back-bottom: #e4e4e6;
  }
  * { box-sizing: border-box; margin: 0; padding: 0; }
  html, body {
    width: 1200px; height: 900px; overflow: hidden;
    background: var(--page);
    font-family: "Exo 2", sans-serif;
  }
  .sheet {
    width: 1200px; height: 900px;
    display: flex; flex-direction: column;
    align-items: center; justify-content: center; gap: 50px;
  }
  .card {
    position: relative;
    width: 680px; height: 390px;
    border-radius: 36px;
    overflow: hidden;
    box-shadow: 0 10px 30px rgba(0,0,0,0.18);
  }
  .card-front {
    background: radial-gradient(ellipse at 60% 35%, var(--navy-light) 0%, var(--navy-dark) 80%);
  }
  .swoosh { position: absolute; inset: 0; width: 100%; height: 100%; }
  .contact-list {
    position: absolute; left: 30px; top: 62px;
    list-style: none; color: var(--white);
    font-size: 15px; letter-spacing: 0.06em;
  }
  .contact-list li { display: flex; align-items: center; gap: 12px; height: 29px; }
  .contact-list svg { width: 16px; height: 16px; fill: var(--white); flex: none; }
  .wordmark {
    position: absolute; right: 50px; top: 100px;
    display: flex; align-items: center; gap: 12px;
    font-weight: 800; font-size: 30px; line-height: 1.05;
    color: var(--white); letter-spacing: 0.04em; text-align: left;
  }
  .wordmark .mark-square { width: 22px; height: 22px; background: var(--white); flex: none; }
  .holder {
    position: absolute; right: 80px; top: 235px;
    color: var(--white); text-align: right;
  }
  .holder-name { font-size: 22px; font-weight: 600; letter-spacing: 0.08em; }
  .holder-title { font-size: 14px; letter-spacing: 0.1em; margin-top: 4px; }
  .card-back {
    background: linear-gradient(180deg, var(--back-top) 0%, var(--back-bottom) 100%);
    display: flex; align-items: center; justify-content: center;
  }
  .card-back .wordmark { position: static; color: var(--ink); font-size: 36px; }
  .card-back .mark-square { background: var(--ink); width: 26px; height: 26px; }
</style>
</head>
<body>
<main class="sheet">
  <section class="card card-front">
    <svg class="swoosh" viewBox="0 0 680 390" preserveAspectRatio="none" aria-hidden="true">
      <path d="M0,248 C200,300 450,322 680,262 L680,390 L0,390 Z" fill="var(--grey-light)"/>
      <path d="M0,262 C220,318 460,338 680,292 L680,390 L0,390 Z" fill="var(--charcoal)"/>
      <path d="M0,280 C220,336 470,354 680,312 L680,390 L0,390 Z" fill="var(--accent)"/>
      <path d="M0,288 C230,344 480,362 680,322 L680,390 L0,390 Z" fill="var(--grey-mid)"/>
    </svg>
    <ul class="contact-list">
      <li><svg viewBox="0 0 24 24"><path d="M6.6 10.8a15.1 15.1 0 0 0 6.6 6.6l2.2-2.2a1 1 0 0 1 1-.25 11.4 11.4 0 0 0 3.6.57 1 1 0 0 1 1 1V20a1 1 0 0 1-1 1A17 17 0 0 1 3 4a1 1 0 0 1 1-1h3.5a1 1 0 0 1 1 1c0 1.25.2 2.45.57 3.57a1 1 0 0 1-.25 1z"/></svg>012 345 6789</li>
      <li><svg viewBox="0 0 24 24"><path d="M7 2h10a2 2 0 0 1 2 2v16a2 2 0 0 1-2 2H7a2 2 0 0 1-2-2V4a2 2 0 0 1 2-2zm0 3v13h10V5zm5 14.2a.9.9 0 1 0 0 1.8.9.9 0 0 0 0-1.8z"/></svg>012 345 6789</li>
      <li><svg viewBox="0 0 24 24"><path d="M6 3h9v5H6zM4 9h16a1 1 0 0 1 1 1v9a1 1 0 0 1-1 1H4a1 1 0 0 1-1-1v-9a1 1 0 0 1 1-1zm3 3v2h2v-2zm4 0v2h2v-2zm-4 4v2h2v-2zm4 0v2h2v-2z"/></svg>012 345 6789</li>
      <li><svg viewBox="0 0 24 24"><path d="M2 5h20v14H2zm2 2v.4l8 5.3 8-5.3V7zm0 2.8V17h16V9.8l-8 5.3z"/></svg>urname@email.com</li>
      <li><svg viewBox="0 0 24 24"><path d="M12 2a10 10 0 1 0 0 20 10 10 0 0 0 0-20zm6.9 6h-3a15 15 0 0 0-1.3-3.9A8 8 0 0 1 18.9 8zM12 4a13 13 0 0 1 1.9 4h-3.8A13 13 0 0 1 12 4zM4.3 14a8 8 0 0 1 0-4h3.4a16 16 0 0 0 0 4zm.8 2h3a15 15 0 0 0 1.3 3.9A8 8 0 0 1 5.1 16zm3-8h-3a8 8 0 0 1 4.3-3.9A15 15 0 0 0 8.1 8zM12 20a13 13 0 0 1-1.9-4h3.8A13 13 0 0 1 12 20zm2.3-6H9.7a14 14 0 0 1 0-4h4.6a14 14 0 0 1 0 4zm.3 5.9a15 15 0 0 0 1.3-3.9h3a8 8 0 0 1-4.3 3.9zm1.7-5.9a16 16 0 0 0 0-4h3.4a8 8 0 0 1 0 4z"/></svg>www.urwebsitename.com</li>
    </ul>
    <div class="wordmark"><span class="mark-square"></span><span>PEARLWOOD<br>FRAMING WORKS</span></div>
    <div class="holder">
      <p class="holder-name">DANIEL MERCER</p>
      <p class="holder-title">FINANCIAL ADVISOR</p>
    </div>
  </section>

  <section class="card card-back">
    <div class="wordmark"><span class="mark-square"></span><span>PEARLWOOD<br>FRAMING WORKS</span></div>
  </section>
</main>
</body>
</html>
```